Law Firm Header Revision

Task: Redesign my law firm Word document header (modern, succinct, logo-first, easy address updates)

I need you to revise and modernize my Microsoft Word document header for Law Office of Bram Holcott, PLLC. The result should look professional and clean on letters (including Letters of Protection), with the logo as the main focus and the text kept succinct.

Goals:
1. Create a modern, minimal header that feels premium and uncluttered.
Make the logo the most visually dominant element.
Reduce the visual weight of the contact/address block so it doesn’t distract from the document.
Make the address easy to change later (I’m moving offices soon) while keeping the same header design.

2. Content to include (keep all info accurate):
Law Office of Bram Holcott, PLLC
615 Pemberly St. Ste #300-214, Houston, TX 77002
Office: 832.555.0143
Direct: 713.555.0187
Fax: 832.555.0129
Bholcottlaw.com

3. Layout requirements:
Provide 3 header style options:
Logo left + contact info right
Centered logo + single concise contact line below
Logo left + firm name prominent + minimal contact line
The primary line near the logo should be minimal (preferably website + main office phone).
The address should be easy to update in one place without redesigning the header. Prefer either:
Move the full address to the footer, or
Put the address in a single dedicated line/block so I can edit it once and keep the layout unchanged.
4. Build constraints:
Must be achievable using standard Microsoft Word tools only (header/footer, tables, alignment, fonts, spacing). No advanced graphics software.
Provide exact header text, plus step-by-step Word instructions for each option:
Font recommendations + sizes
Alignment
Spacing
Table setup (if used)
How to keep it consistent across pages

5. Deliverable:
For each of the 3 options, provide:
The exact header content (with line breaks)
Formatting specs (fonts, sizes, spacing)
Word build steps so I can recreate it reliably and keep the logo as the focal point.

```html
<!DOCTYPE html>
<html lang="en">
<head>
<meta charset="utf-8">
<title>Bram Holcott Law – Letterhead Options</title>
<link rel="stylesheet" href="https://fonts.googleapis.com/css2?family=Poppins:wght@400;500;600&display=swap">
<style>
  :root{
    --navy:#0c2238;
    --ink:#3e4a58;
    --muted:#5b6573;
    --paper:#ffffff;
    --backdrop:#e4e5e7;
    --ghost:#f1f2f2;
  }
  *{box-sizing:border-box;margin:0;padding:0}
  html,body{width:1200px;height:507px;overflow:hidden;background:var(--backdrop)}
  body{font-family:"Poppins",sans-serif;color:var(--ink)}
  .stage{position:absolute;left:0;top:0;width:1981px;height:837px;transform:scale(0.6057);transform-origin:0 0}
  .page{position:absolute;top:23px;width:612px;height:792px;background:var(--paper);overflow:hidden;box-shadow:0 1px 6px rgba(0,0,0,.12)}
  .page--one{left:37px}.page--two{left:685px}.page--three{left:1332px}
  .shapes{position:absolute;inset:0;width:612px;height:792px}
  .shapes .fill{fill:var(--navy)}
  .shapes .ghost{fill:var(--ghost)}
  .abs{position:absolute;white-space:nowrap}

  .brand{display:flex;align-items:center;gap:9px}
  .brand__mark{width:50px;height:56px;background:var(--navy)}
  .brand__name{font-size:25px;font-weight:500;color:var(--navy);letter-spacing:.2px}
  .firm-sub{font-size:11px;letter-spacing:1px;color:var(--muted)}

  .contact{display:flex;align-items:center;gap:8px;font-size:13px;letter-spacing:1.3px;color:var(--ink)}
  .ico{width:18px;height:18px;flex:none}
  .ico .bg{fill:var(--navy)} .ico .gl{fill:var(--paper)} .ico .st{stroke:var(--paper);fill:none;stroke-width:1.6}
  .ico--light .bg{fill:var(--paper)} .ico--light .gl{fill:var(--navy)} .ico--light .st{stroke:var(--navy)}

  .footer-title{font-size:10.5px;font-weight:600;letter-spacing:1.1px;text-transform:uppercase}
  .footer-item{display:flex;gap:12px;font-size:10.5px;line-height:18px;letter-spacing:.9px}
  .footer-item .ico{margin-top:4px;width:20px;height:20px}
  .footer-item strong{font-weight:600;letter-spacing:1.2px}
  .doc-type{font-size:10.5px;letter-spacing:.9px;font-weight:500;text-align:right}
  .light{color:var(--paper)}
  .dark{color:var(--navy)}
  .dark .footer-item span{color:var(--muted)}
</style>
</head>
<body>
<div class="stage">

  <!-- Option 1: logo left, contact right -->
  <section class="page page--one">
    <svg class="shapes" viewBox="0 0 612 792" aria-hidden="true">
      <rect class="fill" x="0" y="7" width="612" height="5"/>
      <polygon class="fill" points="0,7 108,7 88,38 0,38"/>
      <rect class="ghost" x="173" y="269" width="267" height="254"/>
      <polygon class="fill" points="0,667 290,667 321,710 445,710 482,792 0,792"/>
      <polygon class="fill" points="452,710 612,710 612,792 491,792"/>
    </svg>
    <div class="abs brand" style="left:21px;top:50px"><div class="brand__mark"></div><span class="brand__name">Bram Holcott</span></div>
    <div class="abs contact" style="left:437px;top:41px"><svg class="ico" viewBox="0 0 24 24"><rect class="bg" width="24" height="24" rx="4"/><path class="gl" d="M8 6.5c.6 3.8 4.3 8.4 9.5 9.9l-1.6 2.1C10.7 17 6.8 12.7 5.6 7.6z"/></svg>832.555.0143</div>
    <div class="abs contact" style="left:437px;top:71px"><svg class="ico" viewBox="0 0 24 24"><rect class="bg" width="24" height="24" rx="4"/><circle class="st" cx="12" cy="12" r="6.5"/><path class="st" d="M5.5 12h13M12 5.5c-3 3.6-3 9.4 0 13M12 5.5c3 3.6 3 9.4 0 13"/></svg>Bholcottlaw.com</div>

    <div class="abs footer-title light" style="left:30px;top:697px">Law Office of Bram Holcott, PLLC</div>
    <div class="abs footer-item light" style="left:35px;top:731px"><svg class="ico ico--light" viewBox="0 0 24 24"><rect class="bg" width="24" height="24" rx="4"/><path class="gl" d="M12 4a5.5 5.5 0 0 0-5.5 5.5C6.5 14 12 20 12 20s5.5-6 5.5-10.5A5.5 5.5 0 0 0 12 4zm0 7.6a2.1 2.1 0 1 1 0-4.2 2.1 2.1 0 0 1 0 4.2z"/></svg><span>615 Pemberly St. Ste<br>#300-214, Houston,<br>TX 77002</span></div>
    <div class="abs footer-item light" style="left:212px;top:740px"><svg class="ico ico--light" viewBox="0 0 24 24"><rect class="bg" width="24" height="24" rx="4"/><path class="gl" d="M8 6.5c.6 3.8 4.3 8.4 9.5 9.9l-1.6 2.1C10.7 17 6.8 12.7 5.6 7.6z"/></svg><span><strong>DIRECT</strong><br>713.555.0187</span></div>
    <div class="abs footer-item light" style="left:345px;top:739px"><svg class="ico ico--light" viewBox="0 0 24 24"><rect class="bg" width="24" height="24" rx="4"/><path class="gl" d="M7 9h10v8H7zM9 5h6v4H9z"/></svg><span><strong>FAX</strong><br>832.555.0129</span></div>
    <div class="abs doc-type light" style="right:15px;top:729px">Letter Of Production</div>
    <div class="abs doc-type light" style="right:17px;top:763px">Pg : 1</div>
  </section>

  <!-- Option 2: centred logo -->
  <section class="page page--two">
    <svg class="shapes" viewBox="0 0 612 792" aria-hidden="true">
      <rect class="fill" x="0" y="5" width="612" height="5"/>
      <polygon class="fill" points="0,5 108,5 88,36 0,36"/>
      <polygon class="fill" points="523,5 612,5 612,38 500,38"/>
      <rect class="ghost" x="173" y="269" width="267" height="254"/>
      <polyline points="0,675 295,675 317,708 612,708" fill="none" stroke="var(--navy)" stroke-width="3"/>
      <polygon class="fill" points="472,708 612,708 612,792 433,792"/>
    </svg>
    <div class="abs brand" style="left:200px;top:16px"><div class="brand__mark"></div><span class="brand__name">Bram Holcott</span></div>
    <div class="abs contact" style="left:20px;top:50px"><svg class="ico" viewBox="0 0 24 24"><rect class="bg" width="24" height="24" rx="4"/><path class="gl" d="M8 6.5c.6 3.8 4.3 8.4 9.5 9.9l-1.6 2.1C10.7 17 6.8 12.7 5.6 7.6z"/></svg>832.555.0143</div>
    <div class="abs contact" style="right:17px;top:50px"><svg class="ico" viewBox="0 0 24 24"><rect class="bg" width="24" height="24" rx="4"/><circle class="st" cx="12" cy="12" r="6.5"/><path class="st" d="M5.5 12h13M12 5.5c-3 3.6-3 9.4 0 13M12 5.5c3 3.6 3 9.4 0 13"/></svg>Bholcottlaw.com</div>

    <div class="abs footer-title dark" style="left:30px;top:697px">Law Office of Bram Holcott, PLLC</div>
    <div class="abs footer-item dark" style="left:32px;top:724px"><svg class="ico" viewBox="0 0 24 24"><rect class="bg" width="24" height="24" rx="4"/><path class="gl" d="M12 4a5.5 5.5 0 0 0-5.5 5.5C6.5 14 12 20 12 20s5.5-6 5.5-10.5A5.5 5.5 0 0 0 12 4zm0 7.6a2.1 2.1 0 1 1 0-4.2 2.1 2.1 0 0 1 0 4.2z"/></svg><span>615 Pemberly St. Ste<br>#300-214, Houston,<br>TX 77002</span></div>
    <div class="abs footer-item dark" style="left:212px;top:732px"><svg class="ico" viewBox="0 0 24 24"><rect class="bg" width="24" height="24" rx="4"/><path class="gl" d="M8 6.5c.6 3.8 4.3 8.4 9.5 9.9l-1.6 2.1C10.7 17 6.8 12.7 5.6 7.6z"/></svg><span><strong>DIRECT</strong><br>713.555.0187</span></div>
    <div class="abs footer-item dark" style="left:331px;top:731px"><svg class="ico" viewBox="0 0 24 24"><rect class="bg" width="24" height="24" rx="4"/><path class="gl" d="M7 9h10v8H7zM9 5h6v4H9z"/></svg><span><strong>FAX</strong><br>832.555.0129</span></div>
    <div class="abs doc-type light" style="right:15px;top:729px">Letter Of Production</div>
    <div class="abs doc-type light" style="right:17px;top:763px">Pg : 1</div>
  </section>

  <!-- Option 3: logo left with firm name line -->
  <section class="page page--three">
    <svg class="shapes" viewBox="0 0 612 792" aria-hidden="true">
      <rect class="fill" x="0" y="0" width="612" height="4"/>
      <polygon class="fill" points="0,0 96,0 84,13 12,13"/>
      <polygon class="fill" points="265,0 350,0 338,13 277,13"/>
      <polygon class="fill" points="512,0 612,0 600,13 524,13"/>
      <rect class="ghost" x="173" y="269" width="267" height="254"/>
      <polygon class="fill" points="0,671 20,671 28,680 95,680 103,671 292,671 320,710 445,710 482,792 0,792"/>
      <polygon class="fill" points="452,710 497,710 505,725 575,725 583,710 612,710 612,792 491,792"/>
    </svg>
    <div class="abs brand" style="left:26px;top:29px"><div class="brand__mark"></div><span class="brand__name">Bram Holcott</span></div>
    <div class="abs firm-sub" style="left:26px;top:91px">Law Office of Bram Holcott, PLLC</div>
    <div class="abs contact" style="left:437px;top:32px"><svg class="ico" viewBox="0 0 24 24"><rect class="bg" width="24" height="24" rx="4"/><path class="gl" d="M8 6.5c.6 3.8 4.3 8.4 9.5 9.9l-1.6 2.1C10.7 17 6.8 12.7 5.6 7.6z"/></svg>832.555.0143</div>
    <div class="abs contact" style="left:437px;top:62px"><svg class="ico" viewBox="0 0 24 24"><rect class="bg" width="24" height="24" rx="4"/><circle class="st" cx="12" cy="12" r="6.5"/><path class="st" d="M5.5 12h13M12 5.5c-3 3.6-3 9.4 0 13M12 5.5c3 3.6 3 9.4 0 13"/></svg>Bholcottlaw.com</div>

    <div class="abs footer-title light" style="left:30px;top:703px">Law Office of Bram Holcott, PLLC</div>
    <div class="abs footer-item light" style="left:35px;top:731px"><svg class="ico ico--light" viewBox="0 0 24 24"><rect class="bg" width="24" height="24" rx="4"/><path class="gl" d="M12 4a5.5 5.5 0 0 0-5.5 5.5C6.5 14 12 20 12 20s5.5-6 5.5-10.5A5.5 5.5 0 0 0 12 4zm0 7.6a2.1 2.1 0 1 1 0-4.2 2.1 2.1 0 0 1 0 4.2z"/></svg><span>615 Pemberly St. Ste<br>#300-214, Houston,<br>TX 77002</span></div>
    <div class="abs footer-item light" style="left:212px;top:740px"><svg class="ico ico--light" viewBox="0 0 24 24"><rect class="bg" width="24" height="24" rx="4"/><path class="gl" d="M8 6.5c.6 3.8 4.3 8.4 9.5 9.9l-1.6 2.1C10.7 17 6.8 12.7 5.6 7.6z"/></svg><span><strong>DIRECT</strong><br>713.555.0187</span></div>
    <div class="abs footer-item light" style="left:345px;top:739px"><svg class="ico ico--light" viewBox="0 0 24 24"><rect class="bg" width="24" height="24" rx="4"/><path class="gl" d="M7 9h10v8H7zM9 5h6v4H9z"/></svg><span><strong>FAX</strong><br>832.555.0129</span></div>
    <div class="abs doc-type light" style="right:15px;top:741px">Letter Of Production</div>
    <div class="abs doc-type light" style="right:17px;top:764px">Pg : 1</div>
  </section>

</div>
</body>
</html>
```